professional business card design for technology company

We are a small technology consulting firm, specialising in consulting based around Cloud and Managed services. Our colour scheme is yellow, blue and white, as you can see in the logos. Although we are based in melbourne australia, due to the nature of our work, our clients can be located anywhere. We are looking for a clean, professional, positive look - similar to our company logo

Target Market(s)

small business

Industry/Entity Type

Business

Contact Information for Business Card

eye catching, designed to incorporate some level of raised printing. Must contain website address, phone number, name and job title

Requirements
Must have
• Logo (attached) - use of the same colour scheme

```html
<!DOCTYPE html>
<html lang="en">
<head>
<meta charset="utf-8">
<title>Corvane Business Card</title>
<link href="https://fonts.googleapis.com/css2?family=Exo+2:wght@400;500;700&display=swap" rel="stylesheet">
<style>
  :root {
    --backdrop: #e9e6e1;
    --panel-grey: #595959;
    --card-white: #f4f4f4;
    --accent-blue: #2aa5e0;
    --accent-yellow: #f4d83a;
    --ink-light: #ffffff;
    --ink-dark: #4a4a4a;
  }
  html, body {
    margin: 0;
    width: 1200px;
    height: 900px;
    overflow: hidden;
    background: var(--backdrop);
    font-family: "Exo 2", sans-serif;
  }
  .card {
    position: absolute;
    left: 100px;
    top: 165px;
    width: 1000px;
    height: 570px;
    box-shadow: 0 10px 30px rgba(0,0,0,0.18);
    overflow: hidden;
  }
  .card-shapes { position: absolute; inset: 0; }
  .holder { position: absolute; left: 62px; top: 62px; color: var(--ink-light); }
  .holder-name {
    margin: 0;
    font-size: 28px;
    font-weight: 500;
    letter-spacing: 2px;
    text-transform: uppercase;
  }
  .holder-title { margin: 4px 0 0; font-size: 18px; letter-spacing: 0.5px; }
  .address {
    position: absolute; left: 62px; top: 168px;
    color: var(--ink-light); font-size: 19px; line-height: 27px; letter-spacing: 0.8px;
    font-style: normal;
  }
  .contacts {
    position: absolute; left: 62px; top: 262px;
    list-style: none; margin: 0; padding: 0;
    color: var(--ink-light); font-size: 18px; letter-spacing: 1.5px;
  }
  .contacts li { display: flex; align-items: center; height: 31px; }
  .contacts li.small { font-size: 15px; letter-spacing: 0.8px; }
  .contact-icon { width: 18px; height: 18px; margin-right: 14px; fill: var(--ink-light); }
  .brand {
    position: absolute; left: 585px; top: 240px;
    display: flex; align-items: center;
  }
  .brand-dot {
    width: 38px; height: 38px; border-radius: 50%;
    background: var(--accent-blue); margin-right: 18px;
  }
  .brand-name {
    font-size: 88px; font-weight: 700; color: var(--ink-dark);
    letter-spacing: -1px; line-height: 1;
  }
</style>
</head>
<body>
  <div class="card">
    <svg class="card-shapes" width="1000" height="570" viewBox="0 0 1000 570" aria-hidden="true">
      <rect width="1000" height="570" fill="var(--panel-grey)"/>
      <path d="M470,0 C390,160 380,400 530,570 L1000,570 L1000,0 Z" fill="var(--card-white)"/>
      <path d="M520,18 C430,110 395,280 420,440 C430,300 460,150 520,18 Z" fill="var(--accent-blue)"/>
    </svg>

    <div class="holder">
      <h1 class="holder-name">Daniel Whitford</h1>
      <p class="holder-title">Managing Director</p>
    </div>

    <address class="address">27 12th floor,Quay<br>Harbour Street VLT</address>

    <ul class="contacts">
      <li>
        <svg class="contact-icon" viewBox="0 0 20 20"><path d="M4 2l4 1 1 4-2 2c1 2 3 4 5 5l2-2 4 1 1 4-2 1C10 18 2 10 2 4z"/></svg>
        014 552 8130
      </li>
      <li>
        <svg class="contact-icon" viewBox="0 0 20 20"><path d="M6 1h8v18H6z M7.5 3v12h5V3z" fill-rule="evenodd"/></svg>
        014 552 8130
      </li>
      <li>
        <svg class="contact-icon" viewBox="0 0 20 20"><path d="M3 7h14v11H3z M6 2h8v5H6z"/></svg>
        014 552 8130
      </li>
      <li class="small">
        <svg class="contact-icon" viewBox="0 0 20 20"><path d="M2 4h16v12H2z M3 5l7 6 7-6" fill-rule="evenodd"/></svg>
        hello@corvane.net
      </li>
      <li class="small">
        <svg class="contact-icon" viewBox="0 0 20 20"><circle cx="10" cy="10" r="8"/><path d="M2 10h16M10 2c-3 4-3 12 0 16M10 2c3 4 3 12 0 16" stroke="var(--panel-grey)" stroke-width="1.3" fill="none"/></svg>
        www.corvane.net
      </li>
    </ul>

    <div class="brand">
      <span class="brand-dot"></span>
      <span class="brand-name">Corvane</span>
    </div>
  </div>
</body>
</html>
```